Financial Advisor Business Card

This business card is mainly a card for me personally (Marcus Obelwyn) providing services as a Financial Planner and Accountant. My title is: Brightway Mentor
Details provided about Harbourline Financial Advisors on the reverse side of the card is not dominant information, it is provided for ease of contact/communication purposes for prospective clients.
About me: I provide financial advice to my clients however due to regulatory issues in my industry I cannot use the title "Financial Advisor".
Target market is 25 y/o and onwards projecting a cutting edge, innovative and modern marketing influence.
Target Market(s)
25 years old and older
Industry/Entity Type
Financial
Contact Information for Business Card
Front side of business card
Name: Marcus Obelwyn
Position: Brightway Mentor
Accreditations:
Dip FS(FP)
B.Comm
Mobile: 0438 927 583
e-mail: mo@harbourlinefa.com.au
website: www.harbourlinefa.com.au
Reverse side of business card
Name: Marcus Obelwyn
Company: Harbourline Financial Advisors
Position: Senior Accountant
Address:
Level 6, Suite 4
47 Pelham Road
PO Box 718
CHARLESTOWN NSW 2290
Phone: (02) 49718352
Requirements
Must have
- - Cutting edge, innovative, fun but professional, modern marketing design and fonts
- Professional and legible
- Futuristic sharp lines, some with rounded edges
- Preferred Front Card colour scheme: Black background, Silver Text, White Text, Red & Silver lines
- Preferred Reverse Card colour scheme: White background, Silver Text, Black Text, Aqua & Silver lines
Nice to have
- Design a cutting edge logo of my intials as capital letters: MO
with a bigger D and smaller K - Preferred colour is Silver Text
Should not have
- Must not be:
- vintage/classic
- stereotypical accountant/tax agent/money style business card
- old style fonts e.g. times new roman

```html
<!DOCTYPE html>
<html lang="en">
<head>
<meta charset="utf-8">
<title>Marcus Obelwyn – Business Card</title>
<link rel="stylesheet" href="https://fonts.googleapis.com/css2?family=Open+Sans:wght@400;600;700&display=swap">
<style>
  :root {
    --canvas-bg: #ece9e4;
    --card-white: #ffffff;
    --card-black: #0b0c0e;
    --card-black-edge: #1c1f24;
    --accent-blue: #2f7fa6;
    --accent-blue-deep: #1f5f80;
    --name-blue: #2a6f96;
    --text-grey: #4a4d52;
    --text-silver: #a9b0b8;
    --ink: #111214;
  }
  * { margin: 0; padding: 0; box-sizing: border-box; }
  html, body {
    width: 1200px;
    height: 1024px;
    overflow: hidden;
    background: var(--canvas-bg);
    font-family: "Open Sans", Arial, sans-serif;
  }
  .canvas { position: relative; width: 1200px; height: 1024px; }
  .card {
    position: absolute;
    left: 220px;
    width: 760px;
    height: 434px;
    overflow: hidden;
    box-shadow: 0 10px 30px rgba(0,0,0,0.18);
  }

  /* ---------- Front: white card ---------- */
  .card--front { top: 56px; background: var(--card-white); }
  .front__band {
    position: absolute;
    left: 0; right: 70px; bottom: 0;
    height: 36px;
    background: linear-gradient(90deg, var(--accent-blue-deep), var(--accent-blue));
  }
  .front__band-end {
    position: absolute;
    right: 0; bottom: 0;
    width: 70px; height: 36px;
    background: var(--ink);
  }
  .initials {
    display: flex;
    align-items: center;
    gap: 14px;
  }
  .initials__square { flex: none; background: var(--accent-blue); }
  .initials__text {
    font-weight: 600;
    line-height: 1;
    letter-spacing: 2px;
  }
  .front__initials {
    position: absolute;
    left: 70px; top: 222px;
  }
  .front__initials .initials__square { width: 40px; height: 40px; }
  .front__initials .initials__text { font-size: 76px; color: var(--ink); }

  .front__divider {
    position: absolute;
    left: 300px; top: 232px;
    width: 150px; height: 3px;
    background: linear-gradient(90deg, rgba(31,95,128,0), var(--accent-blue-deep));
  }
  .front__details {
    position: absolute;
    left: 480px; top: 96px;
    color: var(--text-grey);
  }
  .details__name {
    font-size: 26px;
    font-weight: 700;
    color: var(--name-blue);
    margin-bottom: 6px;
  }
  .details__title,
  .details__creds { font-size: 17px; line-height: 1.45; }
  .details__contacts { list-style: none; margin-top: 8px; }
  .details__contacts li {
    display: flex;
    align-items: center;
    gap: 10px;
    font-size: 17px;
    line-height: 1.55;
  }
  .contact-icon { width: 14px; height: 14px; flex: none; }

  /* ---------- Back: black card ---------- */
  .card--back {
    top: 534px;
    background: radial-gradient(ellipse at 45% 40%, var(--card-black-edge) 0%, var(--card-black) 70%);
  }
  .back__initials {
    position: absolute;
    left: 0; right: 0; top: 56px;
    justify-content: center;
  }
  .back__initials .initials__square { width: 44px; height: 44px; }
  .back__initials .initials__text { font-size: 90px; color: var(--accent-blue); }

  .back__rule {
    position: absolute;
    left: 230px; right: 230px; top: 196px;
    height: 2px;
    background: linear-gradient(90deg, rgba(169,176,184,0), var(--text-silver), rgba(169,176,184,0));
  }
  .back__info {
    position: absolute;
    left: 70px; right: 70px; top: 226px;
    display: flex;
    justify-content: space-between;
    color: var(--text-silver);
    font-size: 16px;
    line-height: 1.55;
  }
  .back__company { color: #ffffff; font-weight: 600; }
  .back__address { text-align: right; }
  .back__website {
    position: absolute;
    left: 0; right: 0; bottom: 34px;
    text-align: center;
    font-size: 20px;
    letter-spacing: 0.5px;
    color: var(--accent-blue);
  }
</style>
</head>
<body>
<main class="canvas">

  <section class="card card--front" aria-label="Card front">
    <div class="initials front__initials">
      <span class="initials__square" aria-hidden="true"></span>
      <span class="initials__text">MO</span>
    </div>
    <div class="front__divider"></div>

    <div class="front__details">
      <p class="details__name">Marcus Obelwyn</p>
      <p class="details__title">Brightway Mentor</p>
      <p class="details__creds">Dip FS(FP) | B.Comm</p>
      <ul class="details__contacts">
        <li>
          <svg class="contact-icon" viewBox="0 0 14 14" aria-hidden="true">
            <rect x="3" y="1" width="8" height="12" rx="1.5" fill="none" stroke="#4a4d52" stroke-width="1.4"/>
            <line x1="6" y1="11" x2="8" y2="11" stroke="#4a4d52" stroke-width="1.2"/>
          </svg>
          0438 927 583
        </li>
        <li>
          <svg class="contact-icon" viewBox="0 0 14 14" aria-hidden="true">
            <rect x="1" y="3" width="12" height="8" rx="1" fill="#2a6f96"/>
            <polyline points="1.5,3.5 7,8 12.5,3.5" fill="none" stroke="#fff" stroke-width="1.2"/>
          </svg>
          mo@harbourlinefa.com.au
        </li>
        <li>
          <svg class="contact-icon" viewBox="0 0 14 14" aria-hidden="true">
            <circle cx="7" cy="7" r="6" fill="#2a6f96"/>
            <ellipse cx="7" cy="7" rx="2.6" ry="6" fill="none" stroke="#fff" stroke-width="0.9"/>
            <line x1="1" y1="7" x2="13" y2="7" stroke="#fff" stroke-width="0.9"/>
          </svg>
          www.harbourlinefa.com.au
        </li>
      </ul>
    </div>

    <div class="front__band"></div>
    <div class="front__band-end"></div>
  </section>

  <section class="card card--back" aria-label="Card back">
    <div class="initials back__initials">
      <span class="initials__square" aria-hidden="true"></span>
      <span class="initials__text">MO</span>
    </div>
    <div class="back__rule"></div>

    <div class="back__info">
      <div class="back__person">
        <p class="back__company">Harbourline Financial Advisors</p>
        <p>Marcus Obelwyn</p>
        <p>Senior Accountant</p>
        <p>Phone: (02) 49718352</p>
      </div>
      <div class="back__address">
        <p>Level 6, Suite 4</p>
        <p>47 Pelham Road</p>
        <p>PO Box 718</p>
        <p>CHARLESTOWN NSW 2290</p>
      </div>
    </div>

    <p class="back__website">www.marcusobelwyn.com</p>
  </section>

</main>
</body>
</html>
```